wine label for ultra premium vineyard in Ashdown, Upper Calloway, New Zealand

"WREN" is our new wine brand, with grapes grown in our spectacular "ter Hoeven" vineyard. The small, elevated vineyard overlooks a river valley and snowy mountains. We would like a highly elegant label for our 2018 pinot noir wine, which highlights the quality of wine and our very special vineyard location. "WREN" has to be prominent, with secondary emphasis on "ter Hoeven vineyard" and "Ashdown, Upper Calloway". A stylized WREN logo (bird) could be a useful design device instead of the commonly seen illustrated mountain landscape (which is quite common for our local wines). Label size 90 high, 110 wide. Please use a pinot noir / burgundy bottle. See here for vineyard pics, and also below pics for other local wine labels and pics for inspiration / styles. https://www.instagram.com/jan.ter.hoeven/

Target Market(s)

average bottle price for this premium red pinot noir would be aroundUS$40. target market are generally urban professionals aged 25 and older with a high degree of interest in pinot noir wine, and who are familiar with New Zealand pinot noir (ie. already know several brands).

Colors
ed252d

Requirements
Must have
• distinctive label, sophisticated look
Nice to have
• classy white paper stock
Should not have
• label must not get too busy... less but high quality and distinctive is more....

```html
<!DOCTYPE html>
<html lang="en">
<head>
<meta charset="utf-8">
<title>WREN – ter Hoeven vineyard label</title>
<link href="https://fonts.googleapis.com/css2?family=Federo&display=swap" rel="stylesheet">
<style>
  :root {
    --backdrop: #ecebe8;
    --paper: #f4efe4;
    --wine-red: #ed252d;
    --ink-red: #d8202a;
    --art-light: #f6d9d6;
    --art-mid: #e79a98;
  }
  * { margin: 0; padding: 0; box-sizing: border-box; }
  html, body {
    width: 1048px;
    height: 1200px;
    overflow: hidden;
    background: var(--backdrop);
  }
  .label {
    position: absolute;
    left: 94px;
    top: 30px;
    width: 860px;
    height: 1140px;
    background: var(--paper);
    font-family: "Federo", serif;
    color: var(--ink-red);
  }
  .label__frame {
    position: absolute;
    inset: 24px;
    border: 2px solid var(--wine-red);
    border-radius: 20px;
  }
  .brand {
    position: absolute;
    top: 60px;
    left: 0;
    width: 100%;
    display: flex;
    align-items: center;
    justify-content: center;
    gap: 18px;
  }
  .brand__rule {
    width: 190px;
    height: 2px;
    background: var(--wine-red);
  }
  .brand__name {
    font-size: 104px;
    font-weight: 400;
    line-height: 1;
    letter-spacing: 1px;
    transform: scaleX(0.84);
    color: var(--wine-red);
  }
  .estate {
    position: absolute;
    top: 208px;
    width: 100%;
    text-align: center;
    font-size: 44px;
    letter-spacing: 8px;
    line-height: 1;
  }
  .emblem {
    position: absolute;
    left: 255px;
    top: 280px;
    width: 350px;
    height: 630px;
    border-radius: 40% 40% 20% 20%;
    background: radial-gradient(ellipse at 50% 45%, var(--art-mid) 0%, var(--art-light) 65%, var(--paper) 100%);
  }
  .vineyard {
    position: absolute;
    top: 952px;
    width: 100%;
    text-align: center;
    font-size: 44px;
    line-height: 1;
  }
  .vineyard__rule {
    position: absolute;
    top: 1028px;
    left: 236px;
    width: 386px;
    height: 2px;
    background: var(--wine-red);
  }
  .region {
    position: absolute;
    top: 1052px;
    width: 100%;
    text-align: center;
    font-size: 30px;
    line-height: 1;
  }
</style>
</head>
<body>
  <main class="label">
    <div class="label__frame"></div>
    <header class="brand">
      <span class="brand__rule"></span>
      <h1 class="brand__name">WREN</h1>
      <span class="brand__rule"></span>
    </header>
    <p class="estate">TER HOEVEN</p>
    <div class="emblem" role="img" aria-label="Red engraved illustration of a wren perched on a branch"></div>
    <p class="vineyard">ter Hoeven vineyard</p>
    <span class="vineyard__rule"></span>
    <p class="region">Ashdown, Upper Calloway</p>
  </main>
</body>
</html>
```